Tollin Waste Website Design

Our new start-up needs a website design. We plan to help businesses find more sustainable ways to manage their waste. Our initial website aims to gather contact data from potential business customers and comprehensive information from waste facilities and waste transporters. We have a logo design (attached) which we would like included in the website design. I have also attached a number of pages that describe what information should appear on each page as well as a web design brief file that describes the look we are after.

```html
<!DOCTYPE html>
<html lang="en">
<head>
<meta charset="utf-8">
<title>Tollin Waste – Website</title>
<link href="https://fonts.googleapis.com/css2?family=Poppins:wght@400;500;600&family=Open+Sans:wght@400;700&family=Roboto:wght@400;500&display=swap" rel="stylesheet">
<style>
  :root {
    --board: #cfe4b7;
    --green: #6cb52d;
    --green-bright: #8bcf2f;
    --ink: #1c1c1c;
    --muted: #444;
    --white: #ffffff;
    --photo-a: #3d4a2c;
    --photo-b: #2a2d27;
    --photo-c: #8a5a22;
    --footer: rgba(30, 30, 30, 0.55);
  }
  * { box-sizing: border-box; margin: 0; padding: 0; }
  html, body { width: 900px; height: 1200px; overflow: hidden; }
  body { background: var(--board); position: relative; font-family: "Roboto", sans-serif; }

  .screen {
    position: absolute; left: 39px; width: 822px; height: 496px;
    overflow: hidden; color: var(--white);
  }
  .screen--home { top: 67px; }
  .screen--signup { top: 630px; }

  .hero-photo {
    position: absolute; inset: 0;
    background:
      radial-gradient(ellipse 220px 160px at 410px 330px, rgba(160, 100, 30, 0.55), transparent 70%),
      radial-gradient(ellipse 160px 140px at 720px 340px, rgba(120, 120, 120, 0.35), transparent 70%),
      linear-gradient(180deg, #55604a 0%, var(--photo-a) 35%, var(--photo-b) 75%, #1d1f1c 100%);
  }
  .hero-shade { position: absolute; inset: 0; background: rgba(0, 0, 0, 0.25); }

  .site-nav { position: absolute; top: 0; left: 0; right: 0; height: 72px; }
  .brand {
    position: absolute; left: 63px; top: 24px; display: flex; align-items: center; gap: 6px;
    font-family: "Poppins", sans-serif; font-weight: 600; font-size: 17px; color: var(--white);
  }
  .brand-dot { width: 26px; height: 26px; border: 2px solid var(--white); border-radius: 50%; }
  .nav-links { position: absolute; top: 30px; left: 215px; display: flex; gap: 15px;
    font-family: "Poppins", sans-serif; font-size: 10.5px; list-style: none; }
  .social { position: absolute; top: 27px; left: 663px; display: flex; gap: 7px; list-style: none; }
  .social li { width: 19px; height: 19px; border: 1px solid var(--white); border-radius: 50%; }

  .hero-title {
    position: absolute; top: 116px; left: 0; right: 0; text-align: center;
    font-family: "Open Sans", sans-serif; font-weight: 700; font-size: 37px; letter-spacing: -0.5px;
  }
  .hero-sub {
    position: absolute; top: 168px; left: 0; right: 0; text-align: center;
    font-family: "Open Sans", sans-serif; font-size: 27px;
  }

  .roles { list-style: none; }
  .role {
    position: absolute; top: 237px; width: 128px; height: 128px; border-radius: 50%;
    background: rgba(15, 15, 15, 0.82); border: 4px solid var(--green-bright);
    display: flex; flex-direction: column; align-items: center; justify-content: center;
    font-family: "Poppins", sans-serif; font-size: 15px; line-height: 1.2; text-align: center;
  }
  .role svg { margin-bottom: 4px; }
  .role--producers { left: 179px; }
  .role--facilities { left: 341px; }
  .role--transporters { left: 503px; }

  .site-footer {
    position: absolute; left: 0; right: 0; top: 437px; bottom: 0;
    border-top: 1px solid rgba(255, 255, 255, 0.25); background: var(--footer);
    display: flex; align-items: center; justify-content: center;
    font-size: 13px;
  }

  .dim { position: absolute; inset: 0; background: rgba(0, 0, 0, 0.6); }

  .modal {
    position: absolute; left: 143px; top: 100px; width: 537px; height: 286px;
    background: var(--white); border-radius: 12px; color: var(--ink); text-align: center;
  }
  .modal-close { position: absolute; left: 506px; top: 11px; width: 20px; height: 20px; }
  .modal-brand {
    position: absolute; top: 32px; left: 0; right: 0; display: flex; justify-content: center; align-items: center; gap: 8px;
    font-family: "Poppins", sans-serif; font-weight: 600; font-size: 28px; color: #3a3a3a;
  }
  .modal-brand .brand-dot { width: 40px; height: 40px; border: 3px solid var(--green); }
  .modal-title { position: absolute; top: 98px; left: 0; right: 0; font-family: "Poppins", sans-serif; font-weight: 500; font-size: 24px; }
  .modal-text { position: absolute; top: 132px; left: 0; right: 0; font-size: 13px; line-height: 22px; color: var(--muted); }
  .signup-form {
    position: absolute; left: 53px; top: 198px; width: 432px; height: 45px;
    border: 1px solid #555; border-radius: 23px; display: flex; align-items: center; padding: 3px;
  }
  .signup-input { flex: 1; border: 0; outline: 0; font: 12px "Roboto", sans-serif; color: var(--ink); padding-left: 16px; background: none; }
  .signup-input::placeholder { color: var(--ink); }
  .signup-button {
    width: 80px; height: 36px; border: 0; border-radius: 18px; background: var(--green);
    color: var(--white); font: 16px "Poppins", sans-serif;
  }
</style>
</head>
<body>

<section class="screen screen--home">
  <div class="hero-photo" role="img" aria-label="Photo of an orange refuse truck and grey waste bins on a tree-lined street"></div>
  <div class="hero-shade"></div>
  <nav class="site-nav">
    <div class="brand"><span class="brand-dot"></span>Tollin Waste</div>
    <ul class="nav-links"><li>About us</li><li>What we do</li><li>Resources</li><li>Contact us</li></ul>
    <ul class="social"><li></li><li></li><li></li><li></li></ul>
  </nav>
  <h1 class="hero-title">WELCOME TO TOLLIN WASTE</h1>
  <p class="hero-sub">Take control of your waste here</p>
  <ul class="roles">
    <li class="role role--producers">
      <svg width="24" height="30" viewBox="0 0 24 30" fill="none" stroke="#8bcf2f" stroke-width="2.4"><path d="M2 6h20M9 6V2h6v4M4 6l2 22h12l2-22M10 10v14M14 10v14"/></svg>
      Waste<br>Producers
    </li>
    <li class="role role--facilities">
      <svg width="30" height="28" viewBox="0 0 30 28" fill="none" stroke="#8bcf2f" stroke-width="3"><path d="M6 18a9 9 0 0 1 9-13M24 10a9 9 0 0 1-3 14M12 25a9 9 0 0 1-8-4"/><path d="M13 2l3 3-3 3M22 23l-3 2 1 3M3 18l1 3 3-1"/></svg>
      Waste<br>Facilities
    </li>
    <li class="role role--transporters">
      <svg width="46" height="26" viewBox="0 0 46 26" fill="#8bcf2f"><rect x="2" y="2" width="28" height="16" rx="1"/><path d="M32 7h7l5 6v5H32z"/><circle cx="10" cy="21" r="4"/><circle cx="37" cy="21" r="4"/></svg>
      Waste<br>Transporters
    </li>
  </ul>
  <footer class="site-footer">Copyright © 2018. All Rights Reserved</footer>
</section>

<section class="screen screen--signup">
  <div class="hero-photo" role="img" aria-label="Photo of a tree-lined street with waste bins"></div>
  <div class="hero-shade"></div>
  <nav class="site-nav">
    <div class="brand"><span class="brand-dot"></span>Tollin Waste</div>
    <ul class="nav-links"><li>About us</li><li>What we do</li><li>Resources</li><li>Contact us</li></ul>
    <ul class="social"><li></li><li></li><li></li><li></li></ul>
  </nav>
  <footer class="site-footer">Copyright © 2018. All Rights Reserved</footer>
  <div class="dim"></div>

  <div class="modal" role="dialog" aria-label="Sign up for updates">
    <svg class="modal-close" viewBox="0 0 20 20" fill="none" stroke="#222" stroke-width="1.2"><circle cx="10" cy="10" r="9"/><path d="M6 6l8 8M14 6l-8 8"/></svg>
    <div class="modal-brand"><span class="brand-dot"></span>Tollin Waste</div>
    <h2 class="modal-title">Welcome to Tollin Waste.</h2>
    <p class="modal-text">We are just getting started. Please register your email address<br>to receive updates from us</p>
    <form class="signup-form">
      <input class="signup-input" type="email" placeholder="Email address">
      <button class="signup-button" type="button">Signup</button>
    </form>
  </div>
</section>

</body>
</html>
```